Help me make landing pages for my web application that are mobile friendly

I need to make 2 mobile friendly landing pages for an application. The 2 pages will be related. First I need a home page and then I need a working page. I do not want to change the color scheme or logos. Just layout and design.

```html
<!DOCTYPE html>
<html lang="en">
<head>
<meta charset="utf-8">
<title>Assignments – Mobile Screens</title>
<link href="https://fonts.googleapis.com/css2?family=Rubik:wght@400;500;600&family=Roboto:wght@400;500;700&display=swap" rel="stylesheet">
<style>
:root{
  --bg:#2e2640;
  --purple:#6a4fa6;
  --purple-deep:#5e46a0;
  --cyan:#2bb5d8;
  --tint:#eff9fc;
  --ink:#222;
  --muted:#555;
  --line:#d8dde3;
  --green:#5bc52a;
  --red:#f51616;
  --lavender:#d9d0f0;
}
*{box-sizing:border-box;margin:0;padding:0}
html,body{width:702px;height:1200px;overflow:hidden;background:var(--bg)}
body{font-family:"Roboto",Arial,sans-serif;color:var(--ink)}
.stage{position:absolute;left:0;top:0;width:952px;height:1628px;transform:scale(0.7374);transform-origin:0 0;background:var(--bg)}
.phone{position:absolute;top:65px;width:375px;height:1498px;border-radius:40px;overflow:hidden;
  background:linear-gradient(180deg,#6b52ab 0px,#5a78c0 150px,#2fb4d8 332px,#fff 332px,#fff 100%)}
.phone--list{left:74px}
.phone--detail{left:504px}
.status-bar{position:absolute;left:25px;right:25px;top:12px;display:flex;justify-content:space-between;align-items:center;color:#fff;font-size:13px}
.status-bar svg{display:block}
.menu-btn{position:absolute;left:25px;top:45px;width:24px;height:24px;border-radius:50%;background:var(--lavender);display:flex;align-items:center;justify-content:center}
.tabs{position:absolute;left:26px;top:90px;display:flex;gap:11px;white-space:nowrap}
.tab{height:26px;width:118px;border-radius:13px;background:#fff;font-size:11px;display:flex;align-items:center;justify-content:center;color:#333;flex:none}
.tab--active{background:var(--cyan);color:#fff}
.tab--muted{background:var(--lavender);color:#6b5a8e;justify-content:flex-start;padding-left:18px}
.card{position:absolute;left:26px;top:139px;width:324px;background:#fff;border-radius:16px;box-shadow:0 2px 8px rgba(40,60,90,.12)}
.card-title{font-family:"Rubik",sans-serif;font-weight:500;font-size:22px;color:var(--purple);position:absolute;left:24px;top:14px}
.home-bar{position:absolute;left:103px;width:170px;height:4px;border-radius:2px;background:var(--purple)}

/* assignment list */
.assignment{position:absolute;left:24px;width:276px;height:182px}
.sub-tag{position:absolute;left:16px;top:0;width:100px;height:24px;border:1px solid var(--cyan);border-radius:12px;background:#fff;color:var(--cyan);font-size:12px;display:flex;align-items:center;justify-content:center;z-index:2}
.assignment-panel{position:absolute;left:0;top:16px;width:276px;height:166px;border-radius:16px;background:var(--tint)}
.avatar{position:absolute;left:17px;top:17px;width:47px;height:47px;border-radius:50%;background:linear-gradient(135deg,#c9a48a,#6d5040)}
.avatar-check{position:absolute;left:49px;top:49px;width:15px;height:15px;border-radius:50%;background:#fff;border:1.5px solid var(--green);display:flex;align-items:center;justify-content:center}
.person-name{position:absolute;left:74px;top:26px;font-size:13.5px;font-family:"Rubik",sans-serif;color:#222}
.person-role{position:absolute;left:74px;top:45px;font-size:11px;color:var(--cyan)}
.row{position:absolute;left:22px;font-size:12px;display:flex;align-items:center;height:20px}
.row .label{width:81px;color:#333}
.row .colon{width:19px}
.row .value{font-family:"Rubik",sans-serif;color:#222}
.badge{width:80px;height:20px;border-radius:10px;color:#fff;font-size:11.5px;display:flex;align-items:center;justify-content:center}
.badge--complete{background:var(--purple)}
.badge--canceled{background:var(--red)}
.badge--active{background:var(--green)}

/* detail screen */
.info-row{position:absolute;left:23px;font-size:12px;display:flex;align-items:center;height:20px}
.info-row .label{width:130px;color:#222}
.info-row .colon{width:20px}
.info-row .value{color:var(--purple);font-weight:500}
.box{position:absolute;left:25px;width:274px;border-radius:8px}
.box--bordered{border:1px solid var(--line)}
.box-title{position:absolute;left:15px;font-family:"Rubik",sans-serif;font-weight:500;font-size:14px}
.field{position:absolute;background:#fff;border:1px solid var(--line);border-radius:8px;font-size:10px;color:#333;display:flex;align-items:center;padding-left:15px}
.small-label{position:absolute;font-size:9.5px;color:#333}
.pill-btn{position:absolute;height:17px;border-radius:9px;color:#fff;font-size:8.5px;display:flex;align-items:center;justify-content:center;gap:3px}
.clock,.cal{position:absolute;right:9px;top:50%;transform:translateY(-50%)}
.chk{width:9px;height:8px;border:1.2px solid #333;border-radius:2px;background:#fff}
.action-btn{position:absolute;height:24px;border-radius:3px;color:#fff;font-size:10px;font-weight:700;display:flex;align-items:center;justify-content:center}
</style>
</head>
<body>
<div class="stage">

  <!-- Screen 1: My Assignments -->
  <section class="phone phone--list">
    <div class="status-bar"><span>9.36pm</span>
      <span style="display:flex;gap:12px">
        <svg width="14" height="10" viewBox="0 0 14 10"><rect x="0" y="7" width="2" height="3" fill="#fff"/><rect x="4" y="5" width="2" height="5" fill="#fff"/><rect x="8" y="2" width="2" height="8" fill="#fff"/><rect x="12" y="0" width="2" height="10" fill="#fff"/></svg>
        <svg width="14" height="10" viewBox="0 0 14 10"><path d="M1 3.5a9 9 0 0 1 12 0M3 5.5a6 6 0 0 1 8 0M5 7.5a3 3 0 0 1 4 0" stroke="#fff" stroke-width="1.6" fill="none"/><circle cx="7" cy="9" r="1" fill="#fff"/></svg>
        <svg width="18" height="10" viewBox="0 0 18 10"><rect x=".5" y=".5" width="15" height="9" rx="2" stroke="#fff" fill="none"/><rect x="2" y="2" width="10" height="6" fill="#fff"/><rect x="16" y="3" width="2" height="4" fill="#fff"/></svg>
      </span></div>
    <div class="menu-btn"><svg width="12" height="10" viewBox="0 0 12 10"><path d="M1 1h10M1 5h7M1 9h10" stroke="#6a4fa6" stroke-width="1.5"/></svg></div>
    <nav class="tabs">
      <span class="tab tab--active">My Assignments</span>
      <span class="tab">Available Openings</span>
      <span class="tab tab--muted">My Assignments</span>
    </nav>

    <div class="card" style="height:1284px">
      <h1 class="card-title">My Assignments</h1>

      <article class="assignment" style="top:66px">
        <span class="sub-tag">Subbing For:</span>
        <div class="assignment-panel">
          <div class="avatar" role="img" aria-label="Profile photo of Nora Haley"></div>
          <span class="avatar-check"><svg width="8" height="7" viewBox="0 0 8 7"><path d="M1 3.5l2 2 4-4.5" stroke="#5bc52a" stroke-width="1.5" fill="none"/></svg></span>
          <div class="person-name">Nora Haley</div><div class="person-role">Teacher</div>
          <div class="row" style="top:77px"><span class="label">Location</span><span class="colon">:</span><span class="value">KLES</span></div>
          <div class="row" style="top:102px"><span class="label">Status</span><span class="colon">:</span><span class="badge badge--complete">Complete</span></div>
          <div class="row" style="top:127px"><span class="label">Time Slots</span><span class="colon">:</span><span class="value">09/02 -09/02 (1h 0m)</span></div>
        </div>
      </article>

      <article class="assignment" style="top:266px">
        <span class="sub-tag">Subbing For:</span>
        <div class="assignment-panel">
          <div class="avatar" role="img" aria-label="Profile photo placeholder" style="background:linear-gradient(135deg,#d8cfc6,#7a6a5e)"></div>
          <span class="avatar-check"><svg width="8" height="7" viewBox="0 0 8 7"><path d="M1 3.5l2 2 4-4.5" stroke="#5bc52a" stroke-width="1.5" fill="none"/></svg></span>
          <div class="person-name">Extra Duty</div><div class="person-role">Teacher</div>
          <div class="row" style="top:77px"><span class="label">Location</span><span class="colon">:</span><span class="value">KLES</span></div>
          <div class="row" style="top:102px"><span class="label">Status</span><span class="colon">:</span><span class="badge badge--complete">Complete</span></div>
          <div class="row" style="top:127px"><span class="label">Time Slots</span><span class="colon">:</span><span class="value">09/02 -09/02 (1h 0m)</span></div>
        </div>
      </article>

      <article class="assignment" style="top:466px">
        <span class="sub-tag">Subbing For:</span>
        <div class="assignment-panel">
          <div class="avatar" role="img" aria-label="Profile photo of Owen Carter" style="background:linear-gradient(135deg,#e6a0a8,#4a3030)"></div>
          <span class="avatar-check"><svg width="8" height="7" viewBox="0 0 8 7"><path d="M1 3.5l2 2 4-4.5" stroke="#5bc52a" stroke-width="1.5" fill="none"/></svg></span>
          <div class="person-name">Owen Carter</div><div class="person-role">Teacher</div>
          <div class="row" style="top:77px"><span class="label">Location</span><span class="colon">:</span><span class="value">KLES</span></div>
          <div class="row" style="top:102px"><span class="label">Status</span><span class="colon">:</span><span class="badge badge--canceled">Canceled</span></div>
          <div class="row" style="top:127px"><span class="label">Time Slots</span><span class="colon">:</span><span class="value">09/02 -09/02 (1h 0m)</span></div>
        </div>
      </article>

      <article class="assignment" style="top:666px">
        <span class="sub-tag">Subbing For:</span>
        <div class="assignment-panel">
          <div class="avatar" role="img" aria-label="Profile photo of Reid Palmer" style="background:linear-gradient(135deg,#c8ccd2,#4b4440)"></div>
          <span class="avatar-check"><svg width="8" height="7" viewBox="0 0 8 7"><path d="M1 3.5l2 2 4-4.5" stroke="#5bc52a" stroke-width="1.5" fill="none"/></svg></span>
          <div class="person-name">Reid Palmer</div><div class="person-role">Teacher</div>
          <div class="row" style="top:77px"><span class="label">Location</span><span class="colon">:</span><span class="value">KLHS</span></div>
          <div class="row" style="top:102px"><span class="label">Status</span><span class="colon">:</span><span class="badge badge--active">Active</span></div>
          <div class="row" style="top:127px"><span class="label">Time Slots</span><span class="colon">:</span><span class="value">09/02 -09/02 (1h 0m)</span></div>
        </div>
      </article>

      <article class="assignment" style="top:866px">
        <span class="sub-tag">Subbing For:</span>
        <div class="assignment-panel">
          <div class="avatar" role="img" aria-label="Profile photo of Iris Whitmore" style="background:linear-gradient(135deg,#e8d8cc,#8a6048)"></div>
          <span class="avatar-check"><svg width="8" height="7" viewBox="0 0 8 7"><path d="M1 3.5l2 2 4-4.5" stroke="#5bc52a" stroke-width="1.5" fill="none"/></svg></span>
          <div class="person-name">Iris Whitmore</div><div class="person-role">Teacher</div>
          <div class="row" style="top:77px"><span class="label">Location</span><span class="colon">:</span><span class="value">KLES</span></div>
          <div class="row" style="top:102px"><span class="label">Status</span><span class="colon">:</span><span class="badge badge--canceled">Canceled</span></div>
          <div class="row" style="top:127px"><span class="label">Time Slots</span><span class="colon">:</span><span class="value">09/02 -09/02 (1h 0m)</span></div>
        </div>
      </article>

      <article class="assignment" style="top:1066px">
        <span class="sub-tag">Subbing For:</span>
        <div class="assignment-panel">
          <div class="avatar" role="img" aria-label="Profile photo of Miles Dalton" style="background:linear-gradient(135deg,#8fc8e8,#3d3a3a)"></div>
          <span class="avatar-check"><svg width="8" height="7" viewBox="0 0 8 7"><path d="M1 3.5l2 2 4-4.5" stroke="#5bc52a" stroke-width="1.5" fill="none"/></svg></span>
          <div class="person-name">Miles Dalton</div><div class="person-role">Teacher</div>
          <div class="row" style="top:77px"><span class="label">Location</span><span class="colon">:</span><span class="value">KLES</span></div>
          <div class="row" style="top:102px"><span class="label">Status</span><span class="colon">:</span><span class="badge badge--active">Active</span></div>
          <div class="row" style="top:127px"><span class="label">Time Slots</span><span class="colon">:</span><span class="value">09/02 -09/02 (1h 0m)</span></div>
        </div>
      </article>
    </div>
    <div class="home-bar" style="top:1461px"></div>
  </section>

  <!-- Screen 2: Opening Information -->
  <section class="phone phone--detail">
    <div class="status-bar"><span>9.36pm</span>
      <span style="display:flex;gap:12px">
        <svg width="14" height="10" viewBox="0 0 14 10"><rect x="0" y="7" width="2" height="3" fill="#fff"/><rect x="4" y="5" width="2" height="5" fill="#fff"/><rect x="8" y="2" width="2" height="8" fill="#fff"/><rect x="12" y="0" width="2" height="10" fill="#fff"/></svg>
        <svg width="14" height="10" viewBox="0 0 14 10"><path d="M1 3.5a9 9 0 0 1 12 0M3 5.5a6 6 0 0 1 8 0M5 7.5a3 3 0 0 1 4 0" stroke="#fff" stroke-width="1.6" fill="none"/><circle cx="7" cy="9" r="1" fill="#fff"/></svg>
        <svg width="18" height="10" viewBox="0 0 18 10"><rect x=".5" y=".5" width="15" height="9" rx="2" stroke="#fff" fill="none"/><rect x="2" y="2" width="10" height="6" fill="#fff"/><rect x="16" y="3" width="2" height="4" fill="#fff"/></svg>
      </span></div>
    <div class="menu-btn"><svg width="12" height="10" viewBox="0 0 12 10"><path d="M1 1h10M1 5h7M1 9h10" stroke="#6a4fa6" stroke-width="1.5"/></svg></div>
    <nav class="tabs">
      <span class="tab">My Assignments</span>
      <span class="tab tab--active">Available Openings</span>
      <span class="tab tab--muted" style="background:#fff;color:#555">My Assignments</span>
    </nav>

    <div class="card" style="height:1314px">
      <h1 class="card-title">Opening Information</h1>
      <div class="info-row" style="top:57px"><span class="label">Summary</span><span class="colon">:</span><span class="value">Testing-Test</span></div>
      <div class="info-row" style="top:99px"><span class="label">Location</span><span class="colon">:</span><span class="value">KLES</span></div>
      <div class="info-row" style="top:141px"><span class="label">Type</span><span class="colon">:</span><span class="value">Vacancy</span></div>
      <div class="info-row" style="top:183px"><span class="label">Regular Staff</span><span class="colon">:</span><span class="value">Owen Carter</span></div>
      <div class="info-row" style="top:225px"><span class="label">Assignment Category</span><span class="colon">:</span><span class="value">Teacher</span></div>
      <div class="info-row" style="top:267px"><span class="label">Department</span><span class="colon">:</span><span class="value">Science</span></div>
      <div class="info-row" style="top:309px"><span class="label">Description</span></div>
      <div class="box" style="top:337px;height:75px;background:#f2f2f2;border:1px solid var(--line)"></div>

      <div class="box" style="top:427px;height:174px;background:var(--tint)">
        <div class="box-title" style="top:12px;font-size:13.5px">Comments</div>
        <div class="field" style="left:15px;top:38px;width:242px;height:75px;align-items:flex-start;padding-top:10px;padding-left:12px;font-size:9.5px;color:#555">Write a comment or upload a file...</div>
        <span class="pill-btn" style="left:16px;top:120px;width:50px;background:var(--purple)"><svg width="7" height="7" viewBox="0 0 7 7"><path d="M0 3l7-3-2 7-2-3z" fill="#fff"/></svg>Post</span>
        <span class="pill-btn" style="left:71px;top:120px;width:51px;background:var(--cyan)"><svg width="7" height="7" viewBox="0 0 7 7"><path d="M5 2L2.5 4.5a.7.7 0 0 0 1 1L6 3a1.4 1.4 0 0 0-2-2L1.5 3.5a2 2 0 0 0 3 3" stroke="#fff" stroke-width=".8" fill="none"/></svg>Upload</span>
        <div class="small-label" style="left:18px;top:147px;color:#4a55b0;font-size:10px">No comments or files uploaded</div>
      </div>

      <div class="box box--bordered" style="top:617px;height:116px">
        <div class="box-title" style="top:12px">Additional Details</div>
        <div class="small-label" style="left:14px;top:46px">Parking Spot</div>
        <div class="field" style="left:15px;top:67px;width:242px;height:26px"></div>
      </div>

      <div class="box box--bordered" style="top:747px;height:546px">
        <div class="box-title" style="top:12px">Time Slots</div>
        <div class="small-label" style="left:14px;top:43px">Accept</div>
        <div class="small-label" style="left:64px;top:43px">Withdraw</div>
        <div style="position:absolute;left:15px;top:68px;width:242px;height:54px;border:1px solid var(--line);border-radius:6px;overflow:hidden;font-size:10px">
          <div style="position:absolute;left:0;top:0;width:52px;height:26px;background:var(--purple);display:flex;align-items:center;justify-content:center"><span class="chk"></span></div>
          <div style="position:absolute;left:62px;top:7px">Date</div>
          <div style="position:absolute;left:0;top:26px;width:242px;border-top:1px solid var(--line)"></div>
          <div style="position:absolute;left:0;top:26px;width:52px;height:28px;background:#f3f3f3;display:flex;align-items:center;justify-content:center"><span class="chk"></span></div>
          <div style="position:absolute;left:62px;top:35px">03/09/2026</div>
          <svg class="cal" style="top:40px" width="9" height="9" viewBox="0 0 9 9"><rect x=".5" y="1.5" width="8" height="7" rx="1" stroke="#999" fill="none"/><path d="M.5 3.5h8M3 5h1M5 5h1M3 7h1M5 7h1" stroke="#999"/></svg>
        </div>
        <div class="small-label" style="left:13px;top:138px;font-weight:500">From :</div>
        <div class="field" style="left:13px;top:156px;width:242px;height:31px">9:30 PM<svg class="clock" width="9" height="9" viewBox="0 0 9 9"><circle cx="4.5" cy="4.5" r="3.8" stroke="#999" fill="none"/><path d="M4.5 2.5v2h1.5" stroke="#999" fill="none"/></svg></div>
        <div class="small-label" style="left:13px;top:198px;font-weight:500">To :</div>
        <div class="field" style="left:13px;top:216px;width:242px;height:31px">12:30 PM<svg class="clock" width="9" height="9" viewBox="0 0 9 9"><circle cx="4.5" cy="4.5" r="3.8" stroke="#999" fill="none"/><path d="M4.5 2.5v2h1.5" stroke="#999" fill="none"/></svg></div>
        <div class="small-label" style="left:13px;top:268px">Current Assignment</div>
        <div class="small-label" style="left:123px;top:268px">:</div>
        <div class="small-label" style="left:143px;top:268px;font-weight:700">No Assignment</div>
        <div class="small-label" style="left:13px;top:298px">Status</div>
        <div class="small-label" style="left:123px;top:298px">:</div>
        <span class="badge badge--active" style="position:absolute;left:137px;top:296px;width:44px;height:16px;font-size:9px;font-weight:700">Active</span>
        <div class="field" style="left:15px;top:332px;width:242px;height:28px;padding-left:0;overflow:hidden">
          <span style="width:52px;height:100%;background:#f3f3f3;display:flex;align-items:center;justify-content:center;margin-right:10px"><span class="chk"></span></span>03/09/2026
          <svg class="cal" width="9" height="9" viewBox="0 0 9 9"><rect x=".5" y="1.5" width="8" height="7" rx="1" stroke="#999" fill="none"/><path d="M.5 3.5h8M3 5h1M5 5h1M3 7h1M5 7h1" stroke="#999"/></svg>
        </div>
        <div class="small-label" style="left:13px;top:377px;font-weight:500">From :</div>
        <div class="field" style="left:13px;top:395px;width:242px;height:31px">2:30 PM<svg class="clock" width="9" height="9" viewBox="0 0 9 9"><circle cx="4.5" cy="4.5" r="3.8" stroke="#999" fill="none"/><path d="M4.5 2.5v2h1.5" stroke="#999" fill="none"/></svg></div>
        <div class="small-label" style="left:13px;top:437px;font-weight:500">To :</div>
        <div class="field" style="left:13px;top:455px;width:242px;height:31px">4:00 PM<svg class="clock" width="9" height="9" viewBox="0 0 9 9"><circle cx="4.5" cy="4.5" r="3.8" stroke="#999" fill="none"/><path d="M4.5 2.5v2h1.5" stroke="#999" fill="none"/></svg></div>
        <span class="action-btn" style="left:72px;top:498px;width:62px;background:var(--purple)">Save</span>
        <span class="action-btn" style="left:139px;top:498px;width:60px;background:var(--cyan)">Close</span>
      </div>
    </div>
    <div class="home-bar" style="top:1471px"></div>
  </section>

</div>
</body>
</html>
```